Business Card for premium dental clinic

We are a premium dental clinic based in Brasov, Romania with more than 15 year on the market, providing quality dental treatment made by a team of more specialized dentists, working with modern equipment as a solution to beautiful and healthy teeth.

Our current logo for the clinic use 2 square with colors black and gold - dr Ternisu - studio, using family fonts Bodoni, Myriad Pro and Segoe Print.
Depending on the printing we used some gold CMYK background or gold foil picture background or a gold gradient.
We want a business card:
- eye catching business card
- distinguished business card
- premium design
- to keep the color scheme of black and gold
- to attract the customers to spent time reading the information
- modern concept

```html
<!DOCTYPE html>
<html lang="en">
<head>
<meta charset="utf-8">
<title>dr Ternisu studio – business card</title>
<link rel="stylesheet" href="https://fonts.googleapis.com/css2?family=Montserrat:wght@400;500;600&display=swap">
<style>
  :root {
    --stage: #2a2a2a;
    --card-dark: #1f2222;
    --gold: #c9a23a;
    --paper: #ffffff;
    --text-grey: #3a3a3a;
    --text-light: #d8d8d8;
  }
  * { box-sizing: border-box; margin: 0; padding: 0; }
  html, body { width: 1200px; height: 814px; overflow: hidden; }
  body {
    background: var(--stage);
    font-family: "Montserrat", sans-serif;
    position: relative;
  }
  .card {
    position: absolute;
    width: 540px;
    height: 309px;
    overflow: hidden;
    box-shadow: 0 10px 30px rgba(0,0,0,.45);
  }
  .card--back { left: 40px; top: 110px; background: var(--card-dark); }
  .card--front { left: 620px; top: 395px; background: var(--paper); }

  .brand-name {
    position: absolute;
    color: var(--paper);
    font-weight: 500;
    font-size: 28px;
    letter-spacing: 1px;
    white-space: nowrap;
  }
  .card--back .brand-name { left: 50%; top: 88px; transform: translateX(-50%); }
  .card--front .brand-name { right: 48px; top: 58px; font-size: 24px; }

  .address-row {
    position: absolute;
    left: 0; right: 0; top: 228px;
    display: flex;
    align-items: center;
    gap: 16px;
  }
  .address-row__rule { height: 5px; background: var(--gold); flex: 1; }
  .address-row__text { color: var(--text-light); font-size: 12.5px; white-space: nowrap; }

  .front-art { position: absolute; left: 0; top: 0; }

  .contacts {
    position: absolute;
    left: 34px; top: 200px;
    list-style: none;
    font-size: 13px;
    color: var(--text-grey);
  }
  .contacts li { display: flex; align-items: center; gap: 10px; margin-bottom: 7px; }
  .contacts svg { width: 13px; height: 13px; flex: none; }

  .person { position: absolute; left: 300px; top: 238px; }
  .person__name {
    color: var(--gold);
    font-weight: 600;
    font-size: 20px;
    letter-spacing: .5px;
  }
  .person__role { color: var(--text-grey); font-size: 14px; margin-top: 1px; }
</style>
</head>
<body>

  <section class="card card--back" aria-label="Card back">
    <p class="brand-name">dr Ternisu</p>
    <div class="address-row">
      <span class="address-row__rule"></span>
      <span class="address-row__text">Strada Lunga nr 8, 500999 Brasov</span>
      <span class="address-row__rule"></span>
    </div>
  </section>

  <section class="card card--front" aria-label="Card front">
    <svg class="front-art" width="540" height="309" viewBox="0 0 540 309" aria-hidden="true">
      <defs>
        <linearGradient id="goldBand" x1="0" y1="0" x2="1" y2="1">
          <stop offset="0" stop-color="#7d6a26"/>
          <stop offset=".45" stop-color="#b8a24a"/>
          <stop offset=".75" stop-color="#efe29a"/>
          <stop offset="1" stop-color="#a88c35"/>
        </linearGradient>
      </defs>
      <path d="M0,0 H540 V210 C380,255 120,190 0,20 Z" fill="url(#goldBand)"/>
      <path d="M0,0 H540 V190 C380,235 120,170 20,0 Z" fill="#1f2222"/>
    </svg>

    <p class="brand-name">dr Ternisu</p>

    <ul class="contacts">
      <li>
        <svg viewBox="0 0 24 24"><path fill="#c9a23a" d="M6.6 10.8a15 15 0 0 0 6.6 6.6l2.2-2.2c.3-.3.7-.4 1-.2 1.1.4 2.3.6 3.6.6.6 0 1 .4 1 1V20c0 .6-.4 1-1 1A17 17 0 0 1 3 4c0-.6.4-1 1-1h3.5c.6 0 1 .4 1 1 0 1.3.2 2.5.6 3.6.1.3 0 .7-.2 1z"/></svg>
        +40 268 555 019
      </li>
      <li>
        <svg viewBox="0 0 24 24"><rect x="2" y="5" width="20" height="14" fill="#c9a23a"/><path d="M2 5l10 8 10-8" fill="none" stroke="#fff" stroke-width="2"/></svg>
        m.ilescu@drternisu.ro
      </li>
      <li>
        <svg viewBox="0 0 24 24"><circle cx="12" cy="12" r="10" fill="#c9a23a"/><path d="M2 12h20M12 2c3 3 3 17 0 20M12 2c-3 3-3 17 0 20" fill="none" stroke="#fff" stroke-width="1.5"/></svg>
        www.drternisu.ro
      </li>
    </ul>

    <div class="person">
      <p class="person__name">MARA ILESCU</p>
      <p class="person__role">Doctor</p>
    </div>
  </section>

</body>
</html>
```